Business Card Design Project

We need a business card for a new technology services company. We develop software and implement software packages for our business customers and although we will begin with just one or two service offerings, our service offerings will expand over time. Our name comes from the an author, KL Barrow, and his "idea" was that opportunity should be based on ability and achievement, not on social status.

We would like to see a design that is standard in its size and shape, but stands apart in its dramatic color contrasts. The card should not use too many colors - the colors used in the background should highlight the brilliant blues of the logo (see attachment) to dramatic effect. The background should not be white.

If necessary, you can change the color of the words "KL Barrow", but not the word "Idea".

Card size should be U.S. standard 2 inches by 3.5 inches and provide for 1/8 inch bleed area on each side.

We need a design for both sides of the business card, one side communicating the company logo and contact information, the other side being purely graphical, incorporating the logo but no other information.

Contact Information Required:
Kate Brook
KateBrook@klbarrowvista.com
614-387-2259

Target Market(s)

Business executives

Industry/Entity Type

Software

Requirements
Must have
• It must have the full company logo on one side, and at least the graphic element of the logo on the other. Either that or the full logo on both.
Nice to have
• It would be nice to have a design that could work without needing two different textures. For example, it would be nice if the entire card could be shiny, not just parts of the card.

It would also be nice if texture is something we could add later.
Should not have
• The card should not use the color green.

```html
<!DOCTYPE html>
<html lang="en">
<head>
<meta charset="utf-8">
<title>Barrow Vista — Business Card</title>
<link rel="stylesheet" href="https://fonts.googleapis.com/css2?family=Roboto:wght@300;400;700&display=swap">
<style>
  :root {
    --page: #e9e7e4;
    --card-dark: #232323;
    --card-mid: #2e2e2e;
    --brand-blue: #1a9ad6;
    --logo-grey: #b5b5b5;
    --text-light: #f2f2f2;
    --rule: #e6e6e6;
  }
  html, body {
    margin: 0;
    padding: 0;
    width: 1200px;
    height: 750px;
    overflow: hidden;
    background: var(--page);
    font-family: "Roboto", Arial, sans-serif;
  }
  .canvas {
    position: relative;
    width: 1200px;
    height: 750px;
  }
  .card {
    position: absolute;
    top: 220px;
    width: 540px;
    height: 309px;
    border-radius: 22px;
    overflow: hidden;
    background: radial-gradient(ellipse at 40% 40%, var(--card-mid), var(--card-dark) 75%);
    box-shadow: 0 10px 28px rgba(0,0,0,0.28);
  }
  .card--front { left: 40px; }
  .card--back  { left: 620px; }

  /* Front side */
  .brand {
    position: absolute;
    left: 50px;
    top: 141px;
    display: flex;
    align-items: center;
    gap: 10px;
  }
  .brand__dot {
    width: 16px;
    height: 16px;
    border-radius: 50%;
    background: var(--brand-blue);
  }
  .brand__name {
    font-weight: 300;
    font-size: 25px;
    letter-spacing: -0.3px;
    color: var(--logo-grey);
    white-space: nowrap;
  }
  .divider {
    position: absolute;
    left: 290px;
    top: 60px;
    width: 1px;
    height: 190px;
    background: var(--rule);
  }
  .divider__accent {
    position: absolute;
    left: -1px;
    top: 0;
    width: 3px;
    height: 38px;
    background: var(--brand-blue);
  }
  .contact {
    position: absolute;
    left: 306px;
    top: 70px;
  }
  .contact__name {
    margin: 0 0 38px;
    font-weight: 700;
    font-size: 17px;
    letter-spacing: 0.6px;
    color: var(--brand-blue);
    text-transform: uppercase;
  }
  .contact__line {
    display: flex;
    align-items: center;
    gap: 8px;
    margin: 0 0 16px;
    font-weight: 400;
    font-size: 13px;
    color: var(--text-light);
    white-space: nowrap;
  }
  .contact__icon { width: 11px; height: 11px; flex: none; }

  /* Back side */
  .symbol-field {
    position: absolute;
    left: 150px;
    top: 0;
    width: 300px;
    height: 309px;
    background: radial-gradient(ellipse at 50% 48%, rgba(31,111,143,0.75), rgba(31,111,143,0.25) 55%, rgba(31,111,143,0) 72%);
  }
  .back-brand {
    position: absolute;
    left: 0;
    right: 0;
    top: 116px;
    text-align: center;
    font-weight: 300;
    font-size: 62px;
    line-height: 1;
    letter-spacing: -1px;
    color: var(--brand-blue);
    white-space: nowrap;
  }
</style>
</head>
<body>
<main class="canvas">

  <section class="card card--front" aria-label="Business card front">
    <div class="brand">
      <span class="brand__dot"></span>
      <span class="brand__name">Barrow Vista</span>
    </div>

    <div class="divider"><span class="divider__accent"></span></div>

    <div class="contact">
      <h1 class="contact__name">Kate Brook</h1>
      <p class="contact__line">
        <svg class="contact__icon" viewBox="0 0 24 24" aria-hidden="true">
          <path fill="#1a9ad6" d="M6.6 10.8a15.5 15.5 0 0 0 6.6 6.6l2.2-2.2a1 1 0 0 1 1-.25 11.4 11.4 0 0 0 3.6.57 1 1 0 0 1 1 1V20a1 1 0 0 1-1 1A17 17 0 0 1 3 4a1 1 0 0 1 1-1h3.5a1 1 0 0 1 1 1c0 1.250.2 2.450.57 3.6a1 1 0 0 1-.25 1z"/>
        </svg>
        614-387-2259
      </p>
      <p class="contact__line">
        <svg class="contact__icon" viewBox="0 0 24 24" aria-hidden="true">
          <rect x="2" y="5" width="20" height="14" rx="2" fill="#1a9ad6"/>
          <path d="M3 7l9 6 9-6" fill="none" stroke="#232323" stroke-width="2"/>
        </svg>
        KateBrook@klbarrowvista.com
      </p>
    </div>
  </section>

  <section class="card card--back" aria-label="Business card back">
    <div class="symbol-field" role="img" aria-label="Large faint blue brand symbol decoration"></div>
    <div class="back-brand">Barrow Vista</div>
  </section>

</main>
</body>
</html>
```